A clean crisp business card for a Landscape Construction company. Designed to be easy to read contact/ info and also be appealing/interesting, unlike a traditional business card.

Industry/Entity Type

Landscape Construction

Contact Information for Business Card

Company name : Brambleford Landscape Construction, phone number: (877) 62Vista, website:Bramblefordyards.example, Email, sales@bramblefordyards.example

Requirements
Nice to have
• Luxurious finishes/ details…. Icons or emblems next to contact info
Should not have
• Clipart or general pictures

```html
<!DOCTYPE html>
<html lang="en">
<head>
<meta charset="utf-8">
<title>Brambleford Landscape Construction – Business Card</title>
<link rel="stylesheet" href="https://fonts.googleapis.com/css2?family=Cinzel:wght@400;600&family=Open+Sans:wght@400;600&display=swap">
<style>
  :root {
    --page-bg: #c9cbcd;
    --card-black: #131313;
    --brand-green: #9acd3c;
    --brand-blue: #2a6fbf;
    --wave-blue: #2369b8;
    --text-white: #f2f2f2;
  }
  * { box-sizing: border-box; margin: 0; padding: 0; }
  html, body {
    width: 1200px; height: 928px; overflow: hidden;
    background: var(--page-bg);
  }
  .canvas { position: relative; width: 1200px; height: 928px; }
  .card {
    position: absolute; left: 264px; width: 672px; height: 384px;
    background: var(--card-black); border-radius: 16px; overflow: hidden;
  }
  .card--front { top: 59px; }
  .card--back { top: 484px; }

  .brand-name {
    font-family: "Cinzel", serif; font-weight: 400; color: var(--brand-green);
    text-align: center; line-height: 1;
  }
  .card--front .brand-name {
    position: absolute; left: 0; right: 0; top: 118px;
  }
  .brand-name__main { display: block; font-size: 50px; letter-spacing: 1px; }
  .brand-name__sub { display: block; font-size: 17px; letter-spacing: 4px; margin-top: 10px; }

  .front-web {
    position: absolute; left: 0; right: 0; top: 336px; text-align: center;
    font-family: "Cinzel", serif; font-size: 16px; letter-spacing: 2px; color: var(--brand-blue);
  }
  .front-web span { color: var(--brand-green); }

  .person { position: absolute; left: 41px; top: 48px; }
  .person__name {
    font-family: "Cinzel", serif; font-weight: 600; font-size: 28px; letter-spacing: 2px;
    color: var(--brand-green);
  }
  .person__name span { color: var(--brand-blue); }
  .person__role {
    font-family: "Open Sans", sans-serif; font-size: 15px; color: var(--text-white); margin-top: 6px;
  }

  .card--back .brand-name {
    position: absolute; right: 32px; top: 136px; width: 300px;
  }
  .card--back .brand-name__main { font-size: 31px; }
  .card--back .brand-name__sub { font-size: 11px; letter-spacing: 2.6px; margin-top: 6px; }

  .contact-list { position: absolute; left: 41px; top: 199px; list-style: none; }
  .contact-list li {
    display: flex; align-items: center; gap: 8px; height: 32.5px;
    font-family: "Open Sans", sans-serif; font-size: 15px; color: var(--text-white);
  }
  .contact-list li:first-child { letter-spacing: 1px; }
  .contact-list svg { width: 16px; height: 16px; flex: none; }

  .wave { position: absolute; left: 0; top: 0; width: 672px; height: 384px; }
  .address {
    position: absolute; right: 32px; top: 309px; text-align: right;
    font-family: "Open Sans", sans-serif; font-weight: 600; font-size: 15px;
    line-height: 27px; color: var(--text-white);
  }
</style>
</head>
<body>
<main class="canvas">
  <section class="card card--front">
    <h1 class="brand-name">
      <span class="brand-name__main">BRAMBLEFORD</span>
      <span class="brand-name__sub">LANDSCAPE CONSTRUCTION</span>
    </h1>
    <p class="front-web">WWW.<span>BRAMBLEFORDYARDS</span>.EXAMPLE</p>
  </section>

  <section class="card card--back">
    <svg class="wave" viewBox="0 0 672 384" aria-hidden="true">
      <path d="M0 266 C60 330 120 360 220 356 C360 350 520 262 672 270 L672 384 L0 384 Z" fill="var(--wave-blue)"/>
      <path d="M0 266 C60 330 120 360 220 356 C360 350 520 262 672 270" fill="none" stroke="#000" stroke-width="11"/>
      <path d="M0 266 C60 330 120 360 220 356 C360 350 520 262 672 270" fill="none" stroke="var(--brand-green)" stroke-width="6"/>
    </svg>

    <div class="person">
      <h2 class="person__name"><span>O</span>WEN <span>H</span>ARTLEY</h2>
      <p class="person__role">Director</p>
    </div>

    <div class="brand-name">
      <span class="brand-name__main">BRAMBLEFORD</span>
      <span class="brand-name__sub">LANDSCAPE CONSTRUCTION</span>
    </div>

    <ul class="contact-list">
      <li>
        <svg viewBox="0 0 24 24"><path fill="var(--brand-green)" d="M6.6 10.8a15.1 15.1 0 0 0 6.6 6.6l2.2-2.2a1 1 0 0 1 1-.25 11.4 11.4 0 0 0 3.6.57 1 1 0 0 1 1 1V20a1 1 0 0 1-1 1A17 17 0 0 1 3 4a1 1 0 0 1 1-1h3.5a1 1 0 0 1 1 1c0 1.25.2 2.45.57 3.57a1 1 0 0 1-.25 1z"/></svg>
        (877) 62Vista
      </li>
      <li>
        <svg viewBox="0 0 24 24"><rect x="2" y="5" width="20" height="14" rx="1.5" fill="var(--brand-green)"/><path d="M3 6.5l9 6.5 9-6.5" fill="none" stroke="var(--card-black)" stroke-width="1.8"/></svg>
        sales@bramblefordyards.example
      </li>
      <li>
        <svg viewBox="0 0 24 24"><circle cx="12" cy="12" r="10" fill="var(--brand-green)"/><path d="M7 7c2 1 3 3 2 5s1 4 0 6M15 5c-1 2 1 3 3 3M14 14c2 0 3 2 2 4" fill="none" stroke="var(--card-black)" stroke-width="1.6"/></svg>
        www.bramblefordyards.example
      </li>
    </ul>

    <p class="address">4520 Larkspur Valley Rd<br>Suite 118, Fairhaven, OH 45990</p>
  </section>
</main>
</body>
</html>
```